I am looking for a modern, clean and neat design for a reflexology and well being business. The business name is Gralo Tund (this is an old Latin word for wellbeing). The colours I would like are purple, white and grey. I am open to suggestions for pictures such as healing or working hands, a pair of feet, images that represent my business that you may think of....... or maybe you think no images at all would be best? My tag line is: "Relax, Renew, Revive" or "Find you balance......... Relax, Renew, Revive" I can decide which I want so I would like to see what both would look like. I would like space on the back to write the client's appointment date and time (more than once)

```html
<!DOCTYPE html>
<html lang="en">
<head>
<meta charset="utf-8">
<title>Gralo Tund – Business Cards</title>
<link href="https://fonts.googleapis.com/css2?family=Montserrat:wght@700&family=Open+Sans:wght@400;600;700&display=swap" rel="stylesheet">
<style>
  :root {
    --backdrop: #2e2e30;
    --card: #ffffff;
    --ink: #555557;
    --ink-dark: #3a3a3c;
    --lavender: #9fb2e0;
    --rule: #6b6b6d;
  }
  * { box-sizing: border-box; margin: 0; padding: 0; }
  html, body { width: 1200px; height: 900px; overflow: hidden; }
  body {
    background: var(--backdrop);
    font-family: "Open Sans", sans-serif;
    color: var(--ink);
    display: flex;
    flex-direction: column;
    align-items: center;
    justify-content: center;
    gap: 40px;
  }
  .card {
    width: 700px;
    height: 400px;
    background: var(--card);
    position: relative;
  }

  /* Brand wordmark */
  .brand {
    display: flex;
    align-items: center;
    gap: 14px;
    font-family: "Montserrat", sans-serif;
    font-weight: 700;
    color: var(--ink);
    text-transform: uppercase;
    letter-spacing: 0.5px;
  }
  .brand__dot {
    border-radius: 50%;
    background: var(--lavender);
    flex-shrink: 0;
  }

  /* Appointment side */
  .appointment .brand {
    position: absolute;
    top: 70px;
    right: 70px;
    font-size: 44px;
  }
  .appointment .brand__dot { width: 30px; height: 30px; }
  .tagline {
    position: absolute;
    left: 70px;
    top: 160px;
    font-size: 14px;
    font-weight: 600;
    color: var(--ink-dark);
    letter-spacing: 0.5px;
  }
  .appointment__title {
    position: absolute;
    left: 70px;
    top: 185px;
    font-size: 24px;
    font-weight: 600;
    color: var(--lavender);
  }
  .appointment__fields {
    position: absolute;
    left: 110px;
    right: 70px;
    top: 240px;
    list-style: none;
    display: flex;
    flex-direction: column;
    gap: 22px;
  }
  .field {
    display: flex;
    align-items: flex-end;
    font-size: 17px;
    color: var(--ink-dark);
  }
  .field__line {
    flex: 1;
    border-bottom: 1px solid var(--rule);
    margin-left: 4px;
    margin-bottom: 5px;
  }

  /* Contact side */
  .contact .brand {
    position: absolute;
    left: 70px;
    top: 170px;
    font-size: 52px;
  }
  .contact .brand__dot { width: 36px; height: 36px; }
  .person {
    position: absolute;
    left: 440px;
    top: 235px;
  }
  .person__name {
    font-size: 24px;
    font-weight: 700;
    color: var(--ink);
    letter-spacing: 0.5px;
    line-height: 1.1;
  }
  .person__role {
    font-size: 14px;
    color: var(--lavender);
    letter-spacing: 1px;
    margin-bottom: 10px;
  }
  .contact__list { list-style: none; }
  .contact__item {
    display: flex;
    align-items: center;
    gap: 8px;
    font-size: 14px;
    color: var(--ink-dark);
    line-height: 1.45;
  }
  .contact__icon { width: 11px; height: 11px; fill: var(--ink); flex-shrink: 0; }
</style>
</head>
<body>

  <section class="card appointment">
    <div class="brand"><span class="brand__dot"></span>Gralo Tund</div>
    <p class="tagline">RELAX, RENEW, REVIVE</p>
    <h2 class="appointment__title">Appointment:</h2>
    <ul class="appointment__fields">
      <li class="field">Name:<span class="field__line"></span></li>
      <li class="field">Time:<span class="field__line"></span></li>
      <li class="field">Date:<span class="field__line"></span></li>
    </ul>
  </section>

  <section class="card contact">
    <div class="brand"><span class="brand__dot"></span>Gralo Tund</div>
    <div class="person">
      <p class="person__name">MARA QUELL</p>
      <p class="person__role">DIRECTOR</p>
      <ul class="contact__list">
        <li class="contact__item">
          <svg class="contact__icon" viewBox="0 0 24 24" aria-hidden="true"><path d="M6.6 10.8a15 15 0 0 0 6.6 6.6l2.2-2.2c.3-.3.7-.4 1-.2 1.1.4 2.3.6 3.6.6.6 0 1 .4 1 1V20c0 .6-.4 1-1 1C10.6 21 3 13.4 3 4c0-.6.4-1 1-1h3.5c.6 0 1 .4 1 1 0 1.3.2 2.5.6 3.6.1.3 0 .7-.2 1z"/></svg>
          +330 5512-7734
        </li>
        <li class="contact__item">
          <svg class="contact__icon" viewBox="0 0 24 24" aria-hidden="true"><path d="M2 5h20v14H2z M4 7v.4l8 5 8-5V7z" fill-rule="evenodd"/></svg>
          info@gralotund.com
        </li>
        <li class="contact__item">
          <svg class="contact__icon" viewBox="0 0 24 24" aria-hidden="true"><circle cx="12" cy="12" r="10" fill="none" stroke="#555557" stroke-width="2"/><path d="M2 12h20M12 2c3 3 3 17 0 20M12 2c-3 3-3 17 0 20" fill="none" stroke="#555557" stroke-width="1.5"/></svg>
          www.gralotund.com
        </li>
      </ul>
    </div>
  </section>

</body>
</html>
```